Halvik - consultancy website

I need a new design for my webpage/presence [to be functioning with Wordpress - I have a programmer to set it up but not the design idea].
My company is Halvik - a consultancy firm focused on growth management for Swedish SME's primarily;. We call it Leadership toolkit for firms on the rise, kind of a doctor helping small become big. Contentwise, its a simple frontpage + 3-4 subpages with content re company/myself/focus etc. The new site should communicate a fresh, trustworthy take yet simple and functional on all devices [i.e. think UI compatible for mobile/tablet]. Current building parts/form elements are
a) existing logo and text elements
b) existing pictures
c) the yellowish color
colours and new ideas on pictures/positioning are welcome. I prefer a 'full width page' solution with centralised text elements but that's all up to you to suggest. Current site is a quickfix made by myself - now I'm moving it to a new platform so want to take the opportunity to make it
Nothing superspecial as it is a 2-man show; on the other hand I still want to have a modern & fresh reflection of my brand in digital environments. Help me out!
www.halvik-demo.se
Best
Lina Bergqvist

```html
<!DOCTYPE html>
<html lang="en">
<head>
<meta charset="utf-8">
<title>Halvik – Growth management consultancy</title>
<link rel="stylesheet" href="https://fonts.googleapis.com/css2?family=Arimo:ital,wght@0,400;0,700;1,400&display=swap">
<style>
:root{
  --orange:#f0a038;
  --orange-dark:#c98322;
  --ink:#1b1b1b;
  --text:#444;
  --muted:#8a8a8a;
  --line:#e6e6e6;
  --footer:#1e1e1e;
  --footer-bottom:#121212;
  --blue:#3b5a9a;
  --sky:#3fa9e0;
  --red:#db4a39;
  --white:#fff;
}
*{box-sizing:border-box;margin:0;padding:0}
html,body{width:1200px;height:2228px;overflow:hidden}
body{position:relative;font-family:"Arimo",Arial,sans-serif;color:var(--text);background:var(--white)}
.abs{position:absolute}

/* Hero */
.hero{position:absolute;left:0;top:0;width:1200px;height:614px;
  background:linear-gradient(180deg,#b9cfe0 0%,#d9e3ea 22%,#9a8a6a 42%,#b98a45 60%,#8a5e2a 82%,#5a3c1c 100%)}
.brand{position:absolute;left:100px;top:24px}
.brand-name{font-size:46px;font-weight:700;color:#222;letter-spacing:-0.5px;line-height:1}
.brand-tag{font-size:13px;font-weight:700;color:#222;margin-top:6px}
.nav{position:absolute;top:50px;left:0;width:1200px;font-size:15px;color:#222}
.nav a{position:absolute;color:#222;text-decoration:none;white-space:nowrap}
.nav a.active{color:var(--orange)}
.nav .underline{position:absolute;left:588px;top:28px;width:89px;height:2px;background:var(--orange)}
.hero-caption{position:absolute;right:120px;top:436px;text-align:right}
.hero-caption span{display:inline-block;background:rgba(0,0,0,.25);color:#fff;font-size:27px;font-weight:700;padding:2px 4px;line-height:33px}
.hero-btn{position:absolute;left:985px;top:523px;width:105px;height:30px;background:#111;color:#fff;font-size:14px;line-height:30px;text-align:center}
.dots{position:absolute;left:1130px;top:547px;display:flex;gap:7px}
.dots i{width:9px;height:9px;border-radius:50%;border:1px solid #333;background:transparent}
.dots i:first-child{background:#222}

/* About */
.about-title{position:absolute;top:655px;width:1200px;text-align:center;font-size:27px;font-weight:700;color:var(--ink)}
.about-text{position:absolute;left:105px;top:709px;width:990px;text-align:center;font-size:12px;line-height:22px;color:#333}
.btn-orange{position:absolute;left:539px;top:824px;width:120px;height:34px;background:var(--orange);color:#fff;font-size:14px;line-height:34px;text-align:center}

/* Services */
.services{position:absolute;left:98px;top:909px;width:1002px;height:248px;border:1px solid var(--line);display:flex}
.service{position:relative;flex:1;border-right:1px solid var(--line);text-align:center}
.service:last-child{border-right:none}
.service.active{background:var(--orange);color:#fff}
.service.active::after{content:"";position:absolute;left:50%;bottom:-10px;margin-left:-9px;border:9px solid transparent;border-top-color:var(--orange);border-bottom:0}
.service svg{position:absolute;left:50%;top:29px;margin-left:-27px}
.service h3{position:absolute;top:96px;width:100%;font-size:15px;font-weight:700;color:#222}
.service.active h3{color:#fff}
.service p{position:absolute;top:124px;width:100%;font-size:11px;line-height:17px;color:#444}
.service.active p{color:#fff}
.service .more{position:absolute;left:50%;top:194px;margin-left:-50px;width:100px;height:27px;background:#2b2b2b;color:#fff;font-size:11px;line-height:27px}
.service.active .more{background:var(--orange-dark)}

/* Testimonials */
.testimonials{position:absolute;left:0;top:1237px;width:1200px;height:360px;
  background:linear-gradient(180deg,#27202a 0%,#2d2630 45%,#1c1a20 75%,#2a2630 100%)}
.testimonials h2{position:absolute;top:36px;width:100%;text-align:center;color:#fff;font-size:26px;font-weight:700}
.avatar{position:absolute;left:543px;top:83px;width:116px;height:116px;border-radius:50%;background:radial-gradient(circle,#9a9a9a 0%,#6a6a6a 70%);border:5px solid #1a1a1a}
.quote{position:absolute;left:240px;top:222px;width:722px;text-align:center;color:#e4e4e4;font-size:12.5px;font-style:italic;line-height:21px}
.author{position:absolute;top:296px;width:100%;text-align:center;color:#ddd;font-size:11px}
.author b{color:#fff}

/* News */
.news-title{position:absolute;left:97px;top:1641px;font-size:25px;font-weight:700;color:var(--ink)}
.news-arrows{position:absolute;left:1047px;top:1645px;display:flex;gap:8px}
.news-arrows span{width:24px;height:23px;display:block}
.news-card{position:absolute;top:1721px;width:330px;height:130px}
.news-card .thumb{position:absolute;left:0;top:0;width:159px;height:129px}
.news-card .body{position:absolute;left:172px;top:0;width:152px}
.news-card h4{font-size:11.5px;font-weight:700;color:#222;line-height:17px}
.news-card .date{font-size:10px;color:#555;margin-top:5px;padding-bottom:5px;border-bottom:1px solid #ddd}
.news-card p{font-size:10.5px;color:#666;line-height:15px;margin-top:8px}
.news-card .rm{font-size:10px;color:#e0392b;margin-top:8px;display:flex;align-items:center;gap:6px}

/* Footer */
.footer{position:absolute;left:0;top:1948px;width:1200px;height:229px;background:var(--footer);color:#ddd}
.footer h5{position:absolute;top:42px;font-size:14px;font-weight:400;color:#eee}
.divider{position:absolute;top:42px;width:1px;height:157px;background:#3a3a3a}
.social{position:absolute;top:86px;width:72px;height:93px;text-align:center;color:#fff;font-size:13px}
.social i{display:block;width:40px;height:40px;border-radius:50%;background:rgba(255,255,255,.18);margin:8px auto 0}
.social span{display:block;margin-top:22px}
.mail-text{position:absolute;left:535px;top:82px;font-size:11.5px;line-height:20px;color:#aaa}
.mail-input{position:absolute;left:535px;top:131px;width:199px;height:28px;background:#f2f2f2;color:#aaa;font-size:10px;line-height:28px;padding-left:16px}
.mail-btn{position:absolute;left:734px;top:131px;width:34px;height:28px;background:var(--orange)}
.privacy{position:absolute;left:535px;top:168px;font-size:10.5px;color:#888}
.menu{position:absolute;left:971px;top:82px;list-style:none;font-size:11.5px;line-height:21.5px;color:#ddd}
.copyright{position:absolute;left:0;top:2177px;width:1200px;height:51px;background:var(--footer-bottom);color:#777;font-size:11px;text-align:center;line-height:51px}
</style>
</head>
<body>

<header class="hero" role="img" aria-label="Close-up photograph of ripe golden wheat ears against a pale blue sky">
  <div class="brand">
    <div class="brand-name">Halvik</div>
    <div class="brand-tag">Leadership toolkit for firms on the rise</div>
  </div>
  <nav class="nav">
    <a class="active" style="left:614px">Home</a>
    <a style="left:716px">About Us</a>
    <a style="left:829px">Services</a>
    <a style="left:948px">Gallery</a>
    <a style="left:1045px">Contact Us</a>
    <span class="underline"></span>
  </nav>
  <div class="hero-caption">
    <span>We are a consultancy firm focused on growth</span><br>
    <span>management for Swedish SME's</span>
  </div>
  <div class="hero-btn">Read More</div>
  <div class="dots"><i></i><i></i><i></i></div>
</header>

<h1 class="about-title">About Halvik</h1>
<p class="about-text">Lorem ipsum dolor sit amet, consectetur adipiscing elit. Fusce tristique ultricies dui et porta. Sed luctus mauris at dictum auctor. Ut sit amet eleifend tortor, vel fermentum ante. Sed luctus tellus eget tortor mollis, in ullamcorper erat facilisis. Pellentesque bibendum nec nisi ut consectetur. Mauris et elit id est luctus dapibus laoreet scelerisque arcu. Nam varius tincidunt enim quis ultricies. Morbi eleifend, dui faucibus gravida pellentesque, dui lectus tristique ante, et tempor metus ante ut mauris. Quisque feugiat massa ut nisi iaculis pulvinar. Ut euismod mauris enim, ac ultrices massa dignissim ac.</p>
<div class="btn-orange">View More</div>

<section class="services">
  <div class="service">
    <svg width="54" height="54" viewBox="0 0 54 54"><circle cx="27" cy="27" r="25" fill="none" stroke="#333" stroke-width="1.5"/><path d="M18 35h18M20 33v-6M24 33v-9M28 33v-5M32 33v-10M18 20v15" stroke="#333" stroke-width="2" fill="none"/></svg>
    <h3>Growth Management</h3>
    <p>Praesent turpis mauris, aliquet<br>Gravida adipiscing lectus ut rutrum<br>Aenean at posuere risus.</p>
    <div class="more">Read more &nbsp;→</div>
  </div>
  <div class="service">
    <svg width="54" height="54" viewBox="0 0 54 54"><circle cx="27" cy="27" r="25" fill="none" stroke="#333" stroke-width="1.5"/><path d="M17 24h5l10-6v18l-10-6h-5z" fill="#333"/><path d="M20 30l2 7h3l-1-7" fill="#333"/><path d="M35 23q3 4 0 8" stroke="#333" stroke-width="2" fill="none"/></svg>
    <h3>Corporate Communication</h3>
    <p>Praesent turpis mauris, aliquet<br>Gravida adipiscing lectus ut rutrum<br>Aenean at posuere risus.</p>
    <div class="more">Read more &nbsp;→</div>
  </div>
  <div class="service active">
    <svg width="54" height="54" viewBox="0 0 54 54"><circle cx="27" cy="27" r="25" fill="none" stroke="#fff" stroke-width="1.5"/><circle cx="27" cy="27" r="21" fill="none" stroke="#fff" stroke-width="1"/><rect x="19" y="20" width="16" height="15" fill="none" stroke="#fff" stroke-width="1.6"/><path d="M19 24h16M22 18v4M32 18v4M22 27h2M26 27h2M30 27h2M22 31h2M26 31h2M30 31h2" stroke="#fff" stroke-width="1.6"/></svg>
    <h3>Project Management</h3>
    <p>Praesent turpis mauris, aliquet<br>Gravida adipiscing lectus ut rutrum<br>Aenean at posuere risus.</p>
    <div class="more">Read more &nbsp;→</div>
  </div>
  <div class="service">
    <svg width="54" height="54" viewBox="0 0 54 54"><circle cx="27" cy="27" r="25" fill="none" stroke="#333" stroke-width="1.5"/><path d="M18 26h4v10h-4zM22 27l4-8q3 0 2 6h7q2 1 1 3l-2 7q-1 1-3 1h-9" fill="none" stroke="#333" stroke-width="1.8" stroke-linejoin="round"/></svg>
    <h3>Concepetualizing</h3>
    <p>Praesent turpis mauris, aliquet<br>Gravida adipiscing lectus ut rutrum<br>Aenean at posuere risus.</p>
    <div class="more">Read more &nbsp;→</div>
  </div>
</section>

<section class="testimonials" role="img" aria-label="Night photograph of a city skyline beside a suspension bridge">
  <h2>Testimonials</h2>
  <svg class="abs" style="left:30px;top:168px" width="26" height="44" viewBox="0 0 26 44"><path d="M22 2L4 22l18 20" stroke="#fff" stroke-width="1.5" fill="none"/></svg>
  <svg class="abs" style="left:1146px;top:168px" width="26" height="44" viewBox="0 0 26 44"><path d="M4 2l18 20L4 42" stroke="#fff" stroke-width="1.5" fill="none"/></svg>
  <div class="avatar" role="img" aria-label="Portrait photograph of the client giving the testimonial"></div>
  <svg class="abs" style="left:208px;top:193px" width="42" height="30" viewBox="0 0 42 30"><path d="M0 30V14L10 0h6L10 14h8v16zM23 30V14L33 0h6l-6 14h8v16z" fill="#c8c8c8"/></svg>
  <p class="quote">Mauris interdum velit leo, ac porta leo vehicula sed. Maecenas iaculis cursus magna. Vestibulum molestie, urna vel lobortis dictum, lacus nibh varius elit, ac tristique sapien dui sit amet diam. Phasellus hendrerit, augue vitae tristique rhoncus, felis urna blandit mauris, vel egestas ex tellus quis leo. Morbi at lacus in</p>
  <div class="author"><b>Mattias,</b> Lorme ipsum</div>
  <svg class="abs" style="left:962px;top:279px" width="42" height="30" viewBox="0 0 42 30"><path d="M42 0v16L32 30h-6l6-14h-8V0zM19 0v16L9 30H3l6-14H1V0z" fill="#c8c8c8"/></svg>
</section>

<h2 class="news-title">Latest News</h2>
<div class="news-arrows">
  <svg width="24" height="23" viewBox="0 0 24 23"><rect width="24" height="23" fill="#f0a038"/><path d="M14 7l-4 4.5 4 4.5" stroke="#fff" stroke-width="1.6" fill="none"/></svg>
  <svg width="24" height="23" viewBox="0 0 24 23"><rect width="24" height="23" fill="#1b1b1b"/><path d="M10 7l4 4.5-4 4.5" stroke="#fff" stroke-width="1.6" fill="none"/></svg>
</div>

<article class="news-card" style="left:98px">
  <div class="thumb" role="img" aria-label="Photograph of two businessmen reviewing documents at a desk" style="background:linear-gradient(135deg,#eae6e0,#b9a892 60%,#6d6458)"></div>
  <div class="body">
    <h4>Lorem ipsum dolor sit amet, consectetur</h4>
    <div class="date">15/05/2016 &nbsp; - &nbsp; Friday</div>
    <p>Mauris interdum velit leo, ac porta leo vehicula sed. Maece-nas iaculis</p>
    <div class="rm">Read More <svg width="10" height="10" viewBox="0 0 10 10"><circle cx="5" cy="5" r="4.2" fill="none" stroke="#e0392b"/><path d="M3.2 5h3.4M5.2 3.5L6.7 5 5.2 6.5" stroke="#e0392b" fill="none"/></svg></div>
  </div>
</article>
<article class="news-card" style="left:437px">
  <div class="thumb" role="img" aria-label="Photograph of a business handshake over paperwork" style="background:linear-gradient(135deg,#4c6a8c,#a9b9c9 55%,#e6ecf1)"></div>
  <div class="body">
    <h4>Lorem ipsum dolor sit amet, consectetur</h4>
    <div class="date">15/05/2016 &nbsp; - &nbsp; Friday</div>
    <p>Mauris interdum velit leo, ac porta leo vehicula sed. Maece-nas iaculis</p>
    <div class="rm">Read More <svg width="10" height="10" viewBox="0 0 10 10"><circle cx="5" cy="5" r="4.2" fill="none" stroke="#e0392b"/><path d="M3.2 5h3.4M5.2 3.5L6.7 5 5.2 6.5" stroke="#e0392b" fill="none"/></svg></div>
  </div>
</article>
<article class="news-card" style="left:774px">
  <div class="thumb" role="img" aria-label="Photograph of a business team meeting in front of large city windows" style="background:linear-gradient(180deg,#f1efe6,#c9c6b6 55%,#3a3a38)"></div>
  <div class="body">
    <h4>Lorem ipsum dolor sit amet, consectetur</h4>
    <div class="date">15/05/2016 &nbsp; - &nbsp; Friday</div>
    <p>Mauris interdum velit leo, ac porta leo vehicula sed. Maece-nas iaculis</p>
    <div class="rm">Read More <svg width="10" height="10" viewBox="0 0 10 10"><circle cx="5" cy="5" r="4.2" fill="none" stroke="#e0392b"/><path d="M3.2 5h3.4M5.2 3.5L6.7 5 5.2 6.5" stroke="#e0392b" fill="none"/></svg></div>
  </div>
</article>

<footer class="footer">
  <h5 style="left:98px">Let's Connect</h5>
  <div class="social" style="left:98px;background:var(--blue)"><i></i><span>2598</span></div>
  <div class="social" style="left:178px;background:var(--sky)"><i></i><span>4576</span></div>
  <div class="social" style="left:258px;background:var(--red)"><i></i><span>1269</span></div>
  <span class="divider" style="left:437px"></span>
  <h5 style="left:535px">Mailing List</h5>
  <p class="mail-text">Sign up for our mailing list to get latest<br>updates and offers.</p>
  <div class="mail-input">Email address</div>
  <svg class="mail-btn" width="34" height="28" viewBox="0 0 34 28"><rect width="34" height="28" fill="#f0a038"/><path d="M12 14l4 4 7-8" stroke="#fff" stroke-width="2.2" fill="none"/></svg>
  <p class="privacy">We respect your privacy</p>
  <span class="divider" style="left:875px"></span>
  <h5 style="left:971px">Menu</h5>
  <ul class="menu"><li>Home</li><li>About Us</li><li>Services</li><li>Gallery</li><li>Contact Us</li></ul>
</footer>
<div class="copyright">© Copyrights 2015 All Rights Reserved</div>

</body>
</html>
```